Bright Harbor Web Design & Marketing

Will award a 2nd place prize of $100.00 if someone can come up with a logo to match this design!
Updates

Okay, I'm really looking to see some better designs here. What do you think will bring the best designs out? Please remember with all future submissions I'm looking for a cartoon style / illustrator style website. I'm not sure what the technical term is for it, so I uploaded some images in the brief.

Target Market(s)

Small Business Owners

Industry/Entity Type

Marketing

Logo Text

BrightHarbor.com

Number of Pages Required

1 page

Colors

Designer to choose colors to be used in the design.

Requirements
Must have
• Logo should say BrightHarbor.com I would like more than just a text logo. I want some sort of cool custom graphic / icon with it that will look nice on shirts/hats/etc

```html
<!DOCTYPE html>
<html lang="en">
<head>
<meta charset="utf-8">
<title>Bright Harbor Web Design &amp; Marketing</title>
<link href="https://fonts.googleapis.com/css2?family=Open+Sans:wght@400;600;700&family=PT+Sans:wght@400;700&display=swap" rel="stylesheet">
<style>
  :root{
    --white:#ffffff;
    --ink:#222222;
    --nav:#444444;
    --muted:#666666;
    --gold:#c9a05a;
    --gold-line:#c49a52;
    --dark:#1f2124;
    --dark-btn:#2b2b2b;
    --footer-text:#9a9ea3;
    --footer-head:#d3a35a;
    --red:#e2666a;
    --coral:#f2736a;
    --teal:#88dcd4;
    --sky:#a2d8f6;
    --blue-a:#0b5f9e;
    --blue-b:#1b95d4;
    --mix-a:#e38e9c;
    --mix-b:#98a8cf;
    --sq1:#3b5b99;
    --sq2:#2ea6e0;
    --sq3:#1a7bb5;
  }
  *{box-sizing:border-box;margin:0;padding:0}
  html,body{width:1200px;height:2550px;overflow:hidden;background:var(--white)}
  body{position:relative;font-family:"Open Sans",Arial,sans-serif;color:var(--ink)}

  .site-header{position:absolute;top:0;left:0;width:1200px;height:64px;background:var(--white)}
  .brand{position:absolute;left:175px;top:14px;font-family:"PT Sans",Arial,sans-serif;font-weight:700;font-size:29px;letter-spacing:.5px;color:var(--ink)}
  .main-nav{position:absolute;top:24px;left:540px;display:flex;gap:27px;font-size:13px;color:var(--nav)}

  .hero{position:absolute;top:64px;left:0;width:1200px;height:630px;
    background:linear-gradient(180deg,#f1f1f1 0%,#e6e6e6 62%,#dcc08e 64%,#d6b27a 100%)}
  .cloud-edge{position:absolute;left:0;width:1200px;height:50px}

  .services{position:absolute;top:779px;left:223px;display:grid;grid-template-columns:repeat(3,240px);grid-template-rows:repeat(3,159px);column-gap:16px;row-gap:17px}
  .tile{display:flex;flex-direction:column;align-items:center;justify-content:center;color:var(--white);font-size:17px;line-height:22px;text-align:center}
  .tile svg{width:54px;height:54px;margin-bottom:10px}
  .tile--red{background:var(--red)}
  .tile--coral{background:var(--coral)}
  .tile--blue{background:linear-gradient(180deg,var(--blue-a),var(--blue-b))}
  .tile--teal{background:var(--teal)}
  .tile--mix{background:linear-gradient(135deg,var(--mix-a),var(--mix-b))}
  .tile--sky{background:var(--sky)}

  .about{position:absolute;top:1385px;left:0;width:1200px;height:405px;background:var(--gold);color:var(--white);text-align:center}
  .about .map{position:absolute;inset:40px 120px 60px;background:radial-gradient(ellipse at center,rgba(150,110,50,.25),rgba(150,110,50,0) 70%)}
  .about h2{position:absolute;top:42px;width:100%;font-weight:400;font-size:27px}
  .about .intro{position:absolute;top:92px;left:190px;width:820px;font-size:16px;line-height:22px}
  .feature{position:absolute;top:196px;width:290px;text-align:center}
  .feature svg{width:50px;height:50px}
  .feature h3{font-size:13px;font-weight:700;margin-top:6px}
  .feature p{font-size:11px;line-height:15px;margin-top:4px}
  .about-btn{position:absolute;top:361px;left:476px;width:247px;height:44px;background:var(--dark-btn);color:var(--white);font-size:15px;display:flex;align-items:center;padding-left:29px}
  .about-btn span{position:absolute;right:26px;color:#888;font-size:20px}

  .news{position:absolute;top:1825px;left:0;width:1200px;text-align:center}
  .news h2{font-weight:400;font-size:28px;color:var(--ink)}
  .news .rule{width:32px;height:2px;background:var(--gold-line);margin:14px auto 0}
  .news .quote{font-family:Georgia,serif;font-size:44px;color:#d0d0d0;line-height:40px;margin-top:8px}
  .news .excerpt{width:640px;margin:6px auto 0;font-size:12.5px;line-height:20px;color:var(--muted)}
  .news .byline{font-size:11.5px;color:var(--ink);margin-top:12px}
  .news-arrows{display:flex;justify-content:center;gap:6px;margin-top:26px}
  .news-arrows span{width:34px;height:34px;border:1px solid #d5d5d5;border-radius:50%;display:flex;align-items:center;justify-content:center;color:#999;font-size:14px}

  .site-footer{position:absolute;top:2142px;left:0;width:1200px;height:370px;background:linear-gradient(135deg,#25282c,#1b1d20 60%,#23262a);font-family:"PT Sans",Arial,sans-serif}
  .foot-col{position:absolute;top:52px;font-size:12px;color:var(--footer-text)}
  .foot-col h4{font-weight:400;font-size:14px;color:var(--footer-head);margin-bottom:10px}
  .foot-col ul{list-style:none}
  .foot-col li{line-height:20.5px}
  .foot-col--bullets li::before{content:"\2022";color:var(--footer-head);margin-right:6px}
  .foot-col p{line-height:15px;width:320px}
  .footer-mark{position:absolute;top:200px;width:100%;text-align:center;font-weight:700;font-size:27px;letter-spacing:2px;color:#34373b}
  .social{position:absolute;top:298px;left:535px;display:flex;gap:9px}
  .social span{width:37px;height:37px}
  .copyright{position:absolute;top:2512px;left:0;width:1200px;height:38px;background:var(--gold);color:var(--white);font-family:"PT Sans",Arial,sans-serif;font-size:10.5px;display:flex;align-items:center;justify-content:center}
</style>
</head>
<body>

<header class="site-header">
  <div class="brand">BRIGHT HARBOR</div>
  <nav class="main-nav">
    <span>Home</span><span>About Us</span><span>Services &amp; Pricing</span><span>Our Team</span><span>Portfolio</span><span>Contact Us</span>
  </nav>
</header>

<section class="hero" role="img" aria-label="Flat illustration of an office desk with a desktop monitor, keyboard, lamp, binders and books against a white brick wall">
  <svg class="cloud-edge" style="bottom:-2px" viewBox="0 0 1200 50" preserveAspectRatio="none" aria-hidden="true">
    <path fill="#ffffff" d="M0 50 V30 Q30 5 60 25 Q90 0 125 22 Q160 2 195 24 Q230 4 265 22 Q300 0 340 24 Q375 5 410 22 Q445 0 480 24 Q515 4 550 22 Q585 0 625 24 Q660 5 695 22 Q730 0 765 24 Q800 4 835 22 Q870 0 910 24 Q945 5 980 22 Q1015 0 1050 24 Q1085 4 1120 22 Q1160 0 1200 26 V50 Z"/>
  </svg>
</section>

<section class="services">
  <div class="tile tile--red">
    <svg viewBox="0 0 54 54" fill="none" stroke="#fff" stroke-width="3"><circle cx="36" cy="26" r="12"/><circle cx="18" cy="12" r="5" fill="#fff"/><path d="M18 18 L16 34 L10 46 M16 34 L24 46 M17 22 L26 28"/></svg>
    Website Design<br>&amp; Management
  </div>
  <div class="tile tile--red">
    <svg viewBox="0 0 54 54" fill="none" stroke="#fff" stroke-width="3"><rect x="6" y="12" width="34" height="34"/><path d="M20 36 L46 8 M20 36 L18 40 L24 38"/></svg>
    Logo Design &amp;<br>Branding Materials
  </div>
  <div class="tile tile--blue">
    <svg viewBox="0 0 54 54" fill="none" stroke="#fff" stroke-width="2.5"><path d="M19 32 A12 12 0 1 1 35 32 L33 38 H21 Z"/><path d="M22 42 H32 M24 46 H30 M27 4 V8 M8 22 H12 M42 22 H46 M13 9 L16 12 M41 9 L38 12"/></svg>
    Online Store Design<br>&amp; Management
  </div>
  <div class="tile tile--teal">
    <svg viewBox="0 0 54 54" fill="#fff"><circle cx="14" cy="12" r="5"/><circle cx="40" cy="12" r="5"/><circle cx="27" cy="10" r="5"/><rect x="8" y="19" width="12" height="14" rx="3"/><rect x="34" y="19" width="12" height="14" rx="3"/><rect x="21" y="17" width="12" height="12" rx="3"/><rect x="6" y="34" width="42" height="4"/><rect x="12" y="38" width="4" height="10"/><rect x="38" y="38" width="4" height="10"/></svg>
    Local SEO<br>Management
  </div>
  <div class="tile tile--coral">
    <svg viewBox="0 0 54 54" fill="#fff"><rect x="6" y="32" width="8" height="16"/><rect x="18" y="24" width="8" height="24"/><rect x="30" y="28" width="8" height="20"/><rect x="42" y="16" width="8" height="32"/><path d="M6 24 L20 12 L32 18 L46 4" stroke="#fff" stroke-width="3" fill="none"/></svg>
    Search Engine<br>Optimization
  </div>
  <div class="tile tile--mix">
    <svg viewBox="0 0 54 54" fill="none" stroke="#fff" stroke-width="2.5"><circle cx="14" cy="16" r="6"/><circle cx="36" cy="10" r="6"/><circle cx="40" cy="32" r="6"/><circle cx="18" cy="40" r="6"/><path d="M19 19 L34 30 M20 16 L30 12"/></svg>
    Social Media<br>Marketing
  </div>
  <div class="tile tile--mix">
    <svg viewBox="0 0 54 54" fill="#fff"><path d="M8 22 H18 L42 8 V46 L18 32 H8 Z"/><rect x="14" y="32" width="7" height="14"/><path d="M46 20 L52 18 M46 27 H52 M46 34 L52 36" stroke="#fff" stroke-width="3"/></svg>
    Marketing Material<br>&amp; Print Design
  </div>
  <div class="tile tile--red">
    <svg viewBox="0 0 54 54" fill="#fff"><path d="M6 48 Q8 30 22 30 Q36 30 38 48 Z"/><path d="M16 10 H28 V20 Q22 28 16 20 Z"/><circle cx="42" cy="34" r="7" fill="none" stroke="#fff" stroke-width="3"/></svg>
    Outsourcing<br>Management
  </div>
  <div class="tile tile--sky">
    <svg viewBox="0 0 54 54" fill="none" stroke="#fff" stroke-width="5"><rect x="6" y="6" width="26" height="26" rx="5"/><rect x="22" y="22" width="26" height="26" rx="5"/></svg>
    Consulting
  </div>
</section>

<section class="about">
  <svg class="cloud-edge" style="top:-1px" viewBox="0 0 1200 50" preserveAspectRatio="none" aria-hidden="true">
    <path fill="#ffffff" d="M0 0 V20 Q30 45 60 25 Q90 50 125 28 Q160 48 195 26 Q230 46 265 28 Q300 50 340 26 Q375 45 410 28 Q445 50 480 26 Q515 46 550 28 Q585 50 625 26 Q660 45 695 28 Q730 50 765 26 Q800 46 835 28 Q870 50 910 26 Q945 45 980 28 Q1015 50 1050 26 Q1085 46 1120 28 Q1160 50 1200 24 V0 Z"/>
  </svg>
  <div class="map" role="img" aria-label="Faint dotted world map background"></div>
  <h2>About Us</h2>
  <p class="intro">We believe that honesty and integrity come before personal profits. We are a family owned and operated company. Our parents raised us to take care of each other and that's exactly what we've done. We treat each of our clients with the same loyalty and respect that we give each other.</p>

  <div class="feature" style="left:145px">
    <svg viewBox="0 0 50 50" fill="#fff"><circle cx="27" cy="16" r="11"/><text x="27" y="21" font-size="14" text-anchor="middle" fill="#c9a05a" font-family="Arial">$</text><path d="M4 36 H16 L28 40 H44 V46 H22 L4 44 Z"/></svg>
    <h3>100% Risk Free Investment</h3>
    <p>If we are unable to deliver anything that we say we can we will refund you 100% of your investment.</p>
  </div>
  <div class="feature" style="left:453px">
    <svg viewBox="0 0 50 50" fill="#fff"><circle cx="25" cy="14" r="9"/><path d="M8 48 Q10 28 25 28 Q40 28 42 48 Z"/><path d="M25 30 L22 36 L25 46 L28 36 Z" fill="#c9a05a"/></svg>
    <h3>Customer Loyalty Program</h3>
    <p>If we are unable to deliver anything that we say we can we will refund you 100% of your investment.</p>
  </div>
  <div class="feature" style="left:761px">
    <svg viewBox="0 0 50 50" fill="none" stroke="#fff" stroke-width="3"><path d="M40 12 A18 18 0 1 0 44 28"/><path d="M40 4 V12 H32"/><text x="25" y="30" font-size="12" text-anchor="middle" fill="#fff" stroke="none" font-family="Arial" font-weight="700">24/7</text></svg>
    <h3>24/7 U.S Based Customer</h3>
    <p>If we are unable to deliver anything that we say we can we will refund you 100% of your investment.</p>
  </div>

  <div class="about-btn">Learn More About Us<span>&#8250;</span></div>
</section>

<section class="news">
  <h2>Featured News</h2>
  <div class="rule"></div>
  <div class="quote">&#8220;</div>
  <p class="excerpt">Lorem ipsum dolor sit amet, consectetur adipiscing elit, sed do eiusmod tempor incididunt ut labore et dolore magna aliqua. Ut enim ad minim veniam, quis nostrud exercitation...</p>
  <p class="byline">Friday with Us &nbsp;- Friday 25/17</p>
  <div class="news-arrows"><span>&#8249;</span><span>&#8250;</span></div>
</section>

<footer class="site-footer">
  <div class="foot-col foot-col--bullets" style="left:160px">
    <h4>Enterprise</h4>
    <ul><li>Home</li><li>About Us</li><li>Services</li><li>Pricing</li></ul>
  </div>
  <div class="foot-col foot-col--bullets" style="left:335px;top:79px">
    <ul><li>Our Team</li><li>Clients</li><li>Portfolio</li><li>Contact Us</li></ul>
  </div>
  <div class="foot-col" style="left:535px">
    <h4>Social Media</h4>
    <ul><li>Chirply</li><li>Gatherly</li><li>Circlepost</li><li>Vidstream</li></ul>
  </div>
  <div class="foot-col" style="left:733px">
    <h4>Unmatched Personal Service</h4>
    <p>Do you need us to come to your office to help train staff on the management of your new website,content management system, or computer software? That's not a problem.<br>We will come to you and provide hands on training.</p>
  </div>
  <div class="footer-mark">BRIGHT HARBOR</div>
  <div class="social">
    <span style="background:var(--sq1)"></span>
    <span style="background:var(--sq2)"></span>
    <span style="background:var(--sq3)"></span>
  </div>
</footer>

<div class="copyright">Copyrights&copy;2017 Allrights are Reserved</div>

</body>
</html>
```